Moxy Fen needs some awesome stationary

Do you have what it takes to get my brand? You either do or you don't, have a crack at a design and you my just win my business.

I don't want to waste your or my time, so put your creative genius on either a business card or envelope.

I however need a package of stationary that follows the same brand. I will message you to complete the remaining should I like your first submission.

Here is what I need, have a go!

Basically I need the following for my small business based in melbourne.
- Letterhead (printer ready and MS Word)
- Business Card
- Compliments Slip
- Envelope
- Proposal Cover Page (MS Word only)
- Presentation Folder
- Marbled Fox Cards
- Student Name Tent
- Index Cards
- Vell-Ka

I am establishing the brand and it must be modern, professional but also relaxed; that is not formal and not corporate. It represents a company are leaders, but small enough to care and operate like a bunch of friends. We are bringing people and conversations back to business, and turfing out all the bureaucracy and crazy and wasteful procedures. Its about "lets talk and figure it out together and find even better ways".

Target Market(s)

Mainly companies that build software products, but Agile practices are used in many other industries (even graphic design projects)

Industry/Entity Type

Information Technology

Font styles to use
Sans Serif

Colors
3176b5
aaaaaa

Requirements
Must have
• I like curves and circles and not boxes or rectangles.
• I want a colour rich design with my brand colours, but it must be balanced.
• I want more modern than traditional, but simple modern
Should not have
• Not corporate
• Please don't waste my time if your not going to think about it.
• Don't mess with my primary logo
• Don't change my colours
• Don't overlay logo on image

```html
<!DOCTYPE html>
<html lang="en">
<head>
<meta charset="utf-8">
<title>Moxy Fen – Note Sheet and Name Tent</title>
<link rel="stylesheet" href="https://fonts.googleapis.com/css2?family=Open+Sans:wght@400;700&display=swap">
<style>
  :root {
    --backdrop: #8a8b8f;
    --paper: #ffffff;
    --note-pink: #ff8080;
    --rule-solid: #333333;
    --rule-dotted: #8c8c8c;
    --ring: #555555;
    --ink: #222222;
    --ink-soft: #444444;
    --brand-blue: #2c5ba6;
    --brand-grey: #9aa0ab;
    --fold-grey: #c8c8c8;
  }
  * { box-sizing: border-box; margin: 0; padding: 0; }
  html, body {
    width: 1190px; height: 1200px; overflow: hidden;
    background: var(--backdrop);
    font-family: "Open Sans", Arial, sans-serif;
  }
  .canvas { position: relative; width: 1190px; height: 1200px; }

  /* Note sheet */
  .note-sheet {
    position: absolute; left: 320px; top: 164px;
    width: 546px; height: 612px;
    background: var(--paper);
    box-shadow: 0 1px 3px rgba(0,0,0,.3);
  }
  .note-header {
    position: absolute; left: 0; top: 0; width: 100%; height: 96px;
    background: var(--note-pink);
    border-bottom: 1px solid var(--rule-solid);
  }
  .note-rule {
    position: absolute; left: 0; width: 100%;
    border-top: 1px dotted var(--rule-dotted);
  }
  .note-rule--footer { border-top: 1px solid var(--rule-solid); }
  .note-stamp {
    position: absolute; left: 412px; top: 495px;
    width: 110px; height: 110px; border-radius: 50%;
    border: 2px solid var(--ring);
  }
  .note-brand {
    position: absolute; left: 14px; top: 581px;
    display: flex; align-items: center; gap: 5px;
    font-size: 15px; font-weight: 700; color: var(--ink); line-height: 1;
  }
  .note-brand-dot {
    width: 13px; height: 13px; border-radius: 50%; background: var(--ink);
  }
  .note-tagline {
    position: absolute; left: 187px; width: 150px; top: 585px;
    text-align: center; font-size: 15px; color: var(--ink-soft); line-height: 1.2;
  }

  /* Name tent */
  .name-tent { position: absolute; left: 189px; top: 885px; width: 762px; height: 137px; }
  .tent-fold {
    position: absolute; left: 0; top: 0; width: 41px; height: 137px;
    background: var(--fold-grey);
    clip-path: polygon(0 114px, 41px 0, 41px 137px);
  }
  .tent-face {
    position: absolute; left: 41px; top: 0; width: 721px; height: 137px;
    background: var(--paper);
  }
  .tent-band {
    position: absolute; left: 0; top: 0; width: 66px; height: 137px;
    background: linear-gradient(160deg, var(--brand-blue) 55%, var(--brand-grey));
  }
  .tent-brand {
    position: absolute; left: 82px; top: 28px;
    display: flex; flex-direction: column; align-items: flex-start; gap: 6px;
    font-size: 19px; font-weight: 700; color: var(--brand-blue); line-height: 1;
  }
  .tent-brand-dot {
    width: 52px; height: 52px; border-radius: 50%; background: var(--brand-blue);
    margin-left: 10px;
  }
</style>
</head>
<body>
<main class="canvas">

  <section class="note-sheet" aria-label="Vell-Ka note sheet">
    <div class="note-header"></div>
    <div class="note-rule" style="top:174px"></div>
    <div class="note-rule" style="top:241px"></div>
    <div class="note-rule" style="top:309px"></div>
    <div class="note-rule" style="top:375px"></div>
    <div class="note-rule" style="top:444px"></div>
    <div class="note-rule note-rule--footer" style="top:511px"></div>
    <div class="note-stamp"></div>
    <div class="note-brand"><span class="note-brand-dot"></span>Moxy Fen</div>
    <p class="note-tagline">Get It done</p>
  </section>

  <section class="name-tent" aria-label="Student name tent">
    <div class="tent-fold"></div>
    <div class="tent-face">
      <div class="tent-band" role="img" aria-label="Blue and grey curved brand swoosh"></div>
      <div class="tent-brand"><span class="tent-brand-dot"></span>Moxy Fen</div>
    </div>
  </section>

</main>
</body>
</html>
```